Stationary and document suite for consultancy business in Australia called Talmera

I would like to get a suite of documents suitable for my new business called Talmera. I have included the original brief below, however have already selected a design for the logo. I would like to get:
Letter head - simple letter template with "V" logo embossed in background
Word document - standard format with "V" logo embossed in background
Proposal document - bolder pages with cover and back cover, include empty pages with footer as well as contents
Powerpoint presentation - open to ideas
Email signature - banner style or text, open to ideas
Brief that was given for logo (logo not required)
The name of the business is derived from the latin word for green ("Viridis") combined with "co" which is intended to represent a number of different words: collaborative, cooperative, coaching, collective,  construction, consulting, etc.
My objective for the brand is to represent a dynamic, progressive and collaborative business, where our people have fun and enjoy their work.
The objective of our business is to provide consultancy services to construction businesses, mainly aimed at building high performing teams and strategic growth. We will create learning and development tools that businesses can use to increase staff satisfaction and retention. Our future goal is to invest in decarbonisation and sustainability technology for use in the construction industry.
Our target market is construction business leaders and infrastructure owners, who operate road, rail and utility assets. We also want to present as a dynamic, progressive and fun place to work that will be attractive to new employees.

```html
<!DOCTYPE html>
<html lang="en">
<head>
<meta charset="utf-8">
<title>Talmera – Stationery Suite</title>
<link rel="stylesheet" href="https://fonts.googleapis.com/css2?family=Karla:ital,wght@0,400;0,500;0,700;1,400;1,500&family=Montserrat:wght@700;800&display=swap">
<style>
  :root{
    --green:#8dc63f;
    --charcoal:#454547;
    --grey:#77787b;
    --light-grey:#a9a9aa;
    --paper:#ffffff;
    --cover-tint:#f1f5fc;
    --backdrop:#cfcfcf;
    --ink:#2b2b2b;
  }
  *{margin:0;padding:0;box-sizing:border-box}
  html,body{width:1200px;height:1128px;overflow:hidden;background:var(--backdrop)}
  body{position:relative;font-family:'Karla',sans-serif;color:var(--ink)}
  .sheet{position:absolute;background:var(--paper);overflow:hidden;box-shadow:0 1px 3px rgba(0,0,0,.18)}
  .label{position:absolute;font-size:9px;letter-spacing:.06em;color:#222;text-align:center;width:220px}
  .wordmark{position:absolute;font-family:'Karla',sans-serif;font-weight:700;color:var(--grey);letter-spacing:.02em;line-height:1}
  .wordmark.on-dark{color:#fff}
  .contacts{position:absolute;font-size:6.6px;line-height:8.4px;color:var(--grey)}
  .contacts li{list-style:none;display:flex;align-items:center;gap:4px}
  .contacts svg{width:5px;height:5px;fill:var(--green);flex:none}
  .contacts.on-dark{color:#fff}
  .band{position:absolute;left:0;bottom:0;width:100%}
  .band svg{display:block;width:100%;height:100%}

  /* email signatures */
  .sig-name{position:absolute;font-weight:700;color:var(--grey);font-size:10px;letter-spacing:.01em}
  .sig-role{position:absolute;font-size:7px;color:var(--green)}

  /* envelope */
  .envelope-flap{position:absolute;left:0;top:0;width:100%;height:48px}

  /* proposal front */
  .cover-top{position:absolute;left:0;top:0;width:100%;height:300px;background:var(--cover-tint)}
  .cover-year{position:absolute;left:0;width:100%;text-align:center;font-family:'Montserrat',sans-serif;font-weight:800;color:var(--green);font-size:38px;top:147px;line-height:1}
  .cover-title{position:absolute;left:0;width:100%;text-align:center;font-family:'Montserrat',sans-serif;font-weight:800;color:var(--grey);font-size:36px;line-height:34px;letter-spacing:.14em;top:188px}
  .cover-info{position:absolute;left:0;width:100%;text-align:center;color:#fff}
  .cover-info .kicker{font-weight:700;color:var(--green);font-size:10px;margin-top:320px}
  .cover-info .person{font-weight:700;font-size:16px;margin-top:9px;line-height:1}
  .cover-info .role{font-style:italic;font-size:7.5px;margin-top:2px}
  .cover-info .date{font-size:10px;margin-top:14px}
  .cover-info .blurb{font-style:italic;font-size:7px;line-height:9.5px;margin:24px auto 0;width:270px}

  /* proposal inner */
  .inner-heading{position:absolute;left:30px;top:32px;font-weight:700;font-size:14px;color:var(--grey);letter-spacing:.02em}
  .inner-heading span{color:var(--green)}
  .inner-rule{position:absolute;left:30px;width:265px;height:1px;background:var(--green)}
  .photo-slot{position:absolute;left:30px;top:74px;width:269px;height:179px;background:#acacac}
  .inner-copy{position:absolute;left:31px;top:260px;width:268px;font-size:6.3px;line-height:8.6px;color:var(--grey);text-align:justify}
  .inner-copy p+p{margin-top:8px}
  .inner-footer{position:absolute;left:29px;top:434px;width:266px;display:flex;justify-content:space-between;font-size:7px;font-weight:700;color:var(--grey)}
</style>
</head>
<body>

<svg width="0" height="0" style="position:absolute" aria-hidden="true">
  <defs>
    <symbol id="icon-phone" viewBox="0 0 10 10"><path d="M2 0.5 L3.8 2.6 L2.8 3.8 Q3.8 6 6.2 7.2 L7.4 6.2 L9.5 8 L8.4 9.5 Q4.5 9.5 0.5 4.6 Z"/></symbol>
    <symbol id="icon-mail" viewBox="0 0 10 10"><rect x="0" y="2" width="10" height="6.5"/></symbol>
    <symbol id="icon-web" viewBox="0 0 10 10"><circle cx="5" cy="5" r="4.8"/></symbol>
    <symbol id="footer-band" viewBox="0 0 328 32" preserveAspectRatio="none">
      <path d="M0 0 Q164 34 328 8 L328 32 L0 32 Z" fill="#8dc63f"/>
      <path d="M0 8 Q164 38 328 11 L328 32 L0 32 Z" fill="#454547"/>
    </symbol>
  </defs>
</svg>

<!-- Letterhead -->
<section class="sheet letterhead" style="left:84px;top:90px;width:329px;height:425px">
  <div class="wordmark" style="left:26px;top:40px;font-size:20px">Talmera</div>
  <ul class="contacts" style="left:225px;top:34px">
    <li><svg><use href="#icon-phone"/></svg>+61 412 508 934</li>
    <li><svg><use href="#icon-mail"/></svg>rhys@talmera.com.au</li>
    <li><svg><use href="#icon-web"/></svg>talmera.com.au</li>
  </ul>
  <div class="band" style="height:30px"><svg><use href="#footer-band"/></svg></div>
</section>
<div class="label" style="left:142px;top:537px">LETTER HEAD</div>

<!-- Word document -->
<section class="sheet word-doc" style="left:445px;top:90px;width:328px;height:425px">
  <div class="wordmark" style="left:26px;top:43px;font-size:20px">Talmera</div>
  <ul class="contacts" style="left:220px;top:37px">
    <li><svg><use href="#icon-phone"/></svg>+61 412 508 934</li>
    <li><svg><use href="#icon-mail"/></svg>rhys@talmera.com.au</li>
    <li><svg><use href="#icon-web"/></svg>talmera.com.au</li>
  </ul>
</section>
<div class="label" style="left:503px;top:532px">WORD DOCUMENT</div>

<!-- Email signature 01 -->
<section class="sheet email-sig" style="left:820px;top:35px;width:329px;height:97px">
  <div class="wordmark" style="left:40px;top:33px;font-size:24px">Talmera</div>
  <div class="sig-name" style="left:178px;top:18px">RHYS CALLOWAY</div>
  <div class="sig-role" style="left:178px;top:30px">Director</div>
  <ul class="contacts" style="left:178px;top:42px">
    <li><svg><use href="#icon-phone"/></svg>+61 412 508 934</li>
    <li><svg><use href="#icon-mail"/></svg>rhys@talmera.com.au</li>
    <li><svg><use href="#icon-web"/></svg>talmera.com.au</li>
  </ul>
  <div class="band" style="height:22px"><svg><use href="#footer-band"/></svg></div>
</section>
<div class="label" style="left:874px;top:142px">EMAIL SIGNATURE 01</div>

<!-- Email signature 02 -->
<section class="sheet email-sig" style="left:820px;top:187px;width:329px;height:72px">
  <div class="wordmark" style="left:16px;top:21px;font-size:17px">Talmera</div>
  <div class="sig-name" style="left:105px;top:20px">RHYS CALLOWAY</div>
  <div class="sig-role" style="left:140px;top:32px">Director</div>
  <ul class="contacts" style="left:234px;top:18px">
    <li><svg><use href="#icon-phone"/></svg>+61 412 508 934</li>
    <li><svg><use href="#icon-mail"/></svg>rhys@talmera.com.au</li>
    <li><svg><use href="#icon-web"/></svg>talmera.com.au</li>
  </ul>
  <div class="band" style="height:20px"><svg><use href="#footer-band"/></svg></div>
</section>
<div class="label" style="left:874px;top:267px">EMAIL SIGNATURE 02</div>

<!-- Envelope back -->
<section class="sheet envelope-back" style="left:820px;top:286px;width:331px;height:150px;background:#f6f6f6">
  <svg class="envelope-flap" viewBox="0 0 331 48" preserveAspectRatio="none">
    <path d="M0 0 L331 0 L327 30 Q324 47 308 47 L23 47 Q7 47 5 30 Z" fill="#454547"/>
  </svg>
  <div class="wordmark on-dark" style="left:143px;top:18px;font-size:13px">Talmera</div>
</section>

<!-- Envelope front -->
<section class="sheet envelope-front" style="left:803px;top:364px;width:334px;height:153px">
  <div class="wordmark" style="left:19px;top:27px;font-size:16px">Talmera</div>
  <div class="band" style="height:28px"><svg><use href="#footer-band"/></svg></div>
</section>
<div class="label" style="left:859px;top:551px">ENVELOPE FRONT &amp; BACK</div>

<!-- Proposal front -->
<section class="sheet proposal-front" style="left:84px;top:578px;width:329px;height:465px;background:var(--charcoal)">
  <div class="cover-top"></div>
  <div class="wordmark" style="left:0;width:100%;text-align:center;top:60px;font-size:50px">Talmera</div>
  <div class="cover-year">2022</div>
  <div class="cover-title">ANNUAL<br>REPORT</div>
  <svg style="position:absolute;left:0;top:277px;width:100%;height:24px" viewBox="0 0 328 24" preserveAspectRatio="none">
    <path d="M0 0 Q164 20 328 6 L328 24 L0 24 Z" fill="#8dc63f"/>
    <path d="M0 6 Q164 26 328 9 L328 24 L0 24 Z" fill="#454547"/>
  </svg>
  <div class="cover-info">
    <div class="kicker">PREPARED BY</div>
    <div class="person">DANIEL REEVE</div>
    <div class="role">Managing Director</div>
    <div class="date">15, JUNE, 2022</div>
    <p class="blurb">Lorem ipsum dolor sit amet, consectetuer adipiscing elit, sed diam nonummy nibh euismod tincidunt ut laoreet dolore magna aliquam erat volutpat.</p>
  </div>
</section>
<div class="label" style="left:125px;top:1062px">PROPOSAL FRONT</div>

<!-- Proposal back -->
<section class="sheet proposal-back" style="left:444px;top:578px;width:328px;height:465px;background:var(--charcoal)">
  <div class="wordmark on-dark" style="left:0;width:100%;text-align:center;top:82px;font-size:44px">Talmera</div>
  <ul class="contacts on-dark" style="left:187px;top:392px">
    <li><svg><use href="#icon-phone"/></svg>+61 412 508 934</li>
    <li><svg><use href="#icon-mail"/></svg>rhys@talmera.com.au</li>
    <li><svg><use href="#icon-web"/></svg>talmera.com.au</li>
  </ul>
</section>
<div class="label" style="left:484px;top:1062px">PROPOSAL BACK</div>

<!-- Proposal inner page -->
<section class="sheet proposal-inner" style="left:805px;top:578px;width:328px;height:465px">
  <h2 class="inner-heading">ABOUT <span>US</span></h2>
  <div class="wordmark" style="left:247px;top:37px;font-size:12px">Talmera</div>
  <div class="inner-rule" style="top:52px"></div>
  <div class="photo-slot" role="img" aria-label="Photograph placeholder for team or project image"></div>
  <div class="inner-copy">
    <p>Talmera helps construction leaders build teams that perform, stay and grow. We pair practical coaching with clear strategy so that people enjoy their work and projects deliver. Our approach is collaborative, measured and grounded in the realities of road, rail and utility delivery.</p>
    <p>Our services: team diagnostics, leadership coaching and growth planning. Each program starts with listening, then moves to simple tools that managers can use every day. We track retention, satisfaction and delivery outcomes so progress is visible. Over time we aim to invest in decarbonisation and sustainability technology that helps the industry build better, cleaner assets for the communities it serves.</p>
    <p>Our services: team diagnostics, leadership coaching and growth planning. Each program starts with listening.</p>
  </div>
  <div class="inner-rule" style="top:428px;left:29px;width:266px"></div>
  <div class="inner-footer"><span>TALMERA.COM.AU</span><span>1</span></div>
</section>
<div class="label" style="left:846px;top:1059px">PROPOSAL INNER</div>

</body>
</html>
```